Tall Fern Roofing Business Card

Need a business card with the logo that was designed here

Contact Information for Business Card

Name, Title, Phone, Email, Website, Company name

```html
<!DOCTYPE html>
<html lang="en">
<head>
<meta charset="utf-8">
<title>Tall Fern Roofing – Business Card</title>
<link href="https://fonts.googleapis.com/css2?family=Open+Sans:wght@400;600;700&display=swap" rel="stylesheet">
<style>
  :root {
    --backdrop: #222224;
    --brand-blue: #1076c0;
    --bright-blue: #1a7fd0;
    --card-dark: #1e1f23;
    --card-dark-band: #25272d;
    --text-light: #f2f2f2;
    --text-grey: #b8bcc2;
  }
  * { box-sizing: border-box; margin: 0; padding: 0; }
  html, body {
    width: 1200px; height: 780px; overflow: hidden;
    background: var(--backdrop);
    font-family: "Open Sans", Arial, sans-serif;
  }
  .canvas {
    position: relative; width: 1200px; height: 780px;
    display: flex; align-items: center; justify-content: center; gap: 40px;
  }
  .card {
    position: relative; width: 540px; height: 310px;
    border-radius: 22px; overflow: hidden;
  }
  .card-front {
    background: var(--brand-blue);
    display: flex; align-items: center; justify-content: center;
  }
  .card-front .brand-name {
    font-size: 40px; font-weight: 700; color: #0c5d9a; letter-spacing: 0.5px;
  }
  .card-back {
    background: var(--card-dark);
    border-bottom: 5px solid var(--bright-blue);
    color: var(--text-light);
  }
  .contact-band {
    position: absolute; left: 0; right: 0; bottom: 0; height: 92px;
    background: var(--card-dark-band);
  }
  .back-brand {
    position: absolute; left: 32px; top: 42px;
    font-size: 24px; font-weight: 700; color: var(--bright-blue);
  }
  .person {
    position: absolute; right: 40px; top: 40px; text-align: right;
    padding-right: 18px; border-right: 10px solid var(--bright-blue);
  }
  .person-name { font-size: 30px; font-weight: 700; color: var(--bright-blue); line-height: 1.1; }
  .person-title { font-size: 15px; font-weight: 600; color: var(--text-light); margin-top: 4px; }
  .address {
    position: absolute; left: 32px; top: 130px;
    font-size: 15px; line-height: 1.45; color: var(--text-light);
  }
  .contact-list {
    position: absolute; left: 32px; bottom: 14px; list-style: none;
    font-size: 14px; line-height: 1.55; color: var(--text-light);
  }
  .contact-list li { display: flex; align-items: center; gap: 10px; }
  .contact-list svg { width: 14px; height: 14px; fill: var(--bright-blue); flex: none; }
</style>
</head>
<body>
<main class="canvas">
  <section class="card card-front" aria-label="Card front">
    <span class="brand-name">Tall Fern Roofing</span>
  </section>

  <section class="card card-back" aria-label="Card back">
    <div class="contact-band"></div>
    <div class="back-brand">Tall Fern Roofing</div>

    <div class="person">
      <div class="person-name">Dale Morrow</div>
      <div class="person-title">Managing Director</div>
    </div>

    <address class="address" style="font-style:normal">
      1840 Oakline Ave. Suite 310<br>
      Denton, TX 76201
    </address>

    <ul class="contact-list">
      <li>
        <svg viewBox="0 0 24 24" aria-hidden="true"><path d="M6.6 10.8a15.1 15.1 0 0 0 6.6 6.6l2.2-2.2a1 1 0 0 1 1-.25 11.4 11.4 0 0 0 3.6.57 1 1 0 0 1 1 1V20a1 1 0 0 1-1 1A17 17 0 0 1 3 4a1 1 0 0 1 1-1h3.5a1 1 0 0 1 1 1c0 1.25.2 2.45.57 3.57a1 1 0 0 1-.25 1z"/></svg>
        (555) 402-7136
      </li>
      <li>
        <svg viewBox="0 0 24 24" aria-hidden="true"><path d="M2 5h20v14H2zm2 2v.5l8 5 8-5V7zm0 2.9V17h16V9.9l-8 5z"/></svg>
        info@website.com
      </li>
      <li>
        <svg viewBox="0 0 24 24" aria-hidden="true"><path d="M12 2a10 10 0 1 0 0 20 10 10 0 0 0 0-20zm6.9 6h-3a15.6 15.6 0 0 0-1.4-3.6A8 8 0 0 1 18.9 8zM12 4c.8 1.2 1.5 2.5 1.9 4h-3.8c.4-1.5 1.1-2.8 1.9-4zM4.3 14a8.2 8.2 0 0 1 0-4h3.4a16.5 16.5 0 0 0 0 4zm.8 2h3a15.6 15.6 0 0 0 1.4 3.6A8 8 0 0 1 5.1 16zm3-8h-3a8 8 0 0 1 4.4-3.6A15.6 15.6 0 0 0 8.1 8zM12 20c-.8-1.2-1.5-2.5-1.9-4h3.8c-.4 1.5-1.1 2.8-1.9 4zm2.3-6H9.7a14.7 14.7 0 0 1 0-4h4.6a14.7 14.7 0 0 1 0 4zm.2 5.6a15.6 15.6 0 0 0 1.4-3.6h3a8 8 0 0 1-4.4 3.6zm1.8-5.6a16.5 16.5 0 0 0 0-4h3.4a8.2 8.2 0 0 1 0 4z"/></svg>
        www.website.com
      </li>
    </ul>
  </section>
</main>
</body>
</html>
```